1876 Basins & Spouts Business Card

I'm wanting to get a business card designed. Our business is 1876 Basins & Spouts
Details for the card:

1876 Basins & Spouts
Name: Harold Vesk
Email: harold@1876basinsandspouts.com.au
Website: www.1876basinsandspouts.com.au
Mobile: 0438 260 947
Phone: 02 7481 3926

Font of Basins & Spouts is called Snell Roundhand. Not sue what font logo text is.

I'm thinking two sided but it doesn't have to be.

```html
<!DOCTYPE html>
<html lang="en">
<head>
<meta charset="utf-8">
<title>1876 Basins &amp; Spouts – Business Card</title>
<link rel="stylesheet" href="https://fonts.googleapis.com/css2?family=Pinyon+Script&family=Open+Sans:wght@400&display=swap">
<style>
  :root {
    --backdrop: #7b4a22;
    --card-dark: #231f20;
    --card-light: #ffffff;
    --ink-light: #ececec;
    --ink-dark: #111111;
    --rule: #6d6a6b;
    --icon-fill: #f2f2f2;
  }
  html, body {
    margin: 0;
    width: 1200px;
    height: 900px;
    overflow: hidden;
    background: var(--backdrop);
  }
  .canvas {
    position: relative;
    width: 1200px;
    height: 900px;
  }
  .card {
    position: absolute;
    box-shadow: 3px 4px 6px rgba(0,0,0,0.45);
  }
  .card--back {
    left: 330px; top: 90px;
    width: 555px; height: 343px;
    background: var(--card-dark);
    color: var(--ink-light);
  }
  .card--front {
    left: 330px; top: 470px;
    width: 558px; height: 342px;
    background: var(--card-light);
    color: var(--ink-dark);
  }
  .holder-name {
    position: absolute;
    top: 78px; left: 0; right: 0;
    text-align: center;
    font-family: "Pinyon Script", cursive;
    font-size: 38px;
    line-height: 46px;
    margin: 0;
    font-weight: 400;
  }
  .icon-row {
    position: absolute;
    top: 145px; left: 175px;
    width: 196px; height: 20px;
    display: flex; align-items: center; justify-content: center; gap: 4px;
  }
  .icon-row__rule {
    flex: 1;
    height: 1px;
    background: var(--rule);
  }
  .icon-row__rule--left { margin-right: 2px; }
  .icon-row__rule--right { margin-left: 2px; }
  .icon {
    width: 20px; height: 20px;
    display: block;
  }
  .contact-list {
    position: absolute;
    top: 176px; left: 0; right: 0;
    margin: 0; padding: 0;
    list-style: none;
    text-align: center;
    font-family: "Open Sans", sans-serif;
    font-size: 16px;
    line-height: 20px;
  }
  .brand {
    position: absolute;
    top: 140px; left: 88px;
    display: flex;
    align-items: flex-start;
    gap: 16px;
  }
  .brand__mark {
    width: 46px; height: 46px;
    border-radius: 50%;
    border: 2px solid var(--ink-dark);
    box-sizing: border-box;
    flex: none;
    margin-top: 2px;
  }
  .brand__name {
    font-family: "Open Sans", sans-serif;
    font-size: 30px;
    line-height: 40px;
    margin: 0;
    font-weight: 400;
    white-space: nowrap;
  }
  .brand__tagline {
    font-family: "Open Sans", sans-serif;
    font-size: 11px;
    line-height: 14px;
    margin: 8px 0 0 0;
    white-space: nowrap;
  }
</style>
</head>
<body>
<main class="canvas">
  <section class="card card--back" aria-label="Card back with contact details">
    <h1 class="holder-name">Harold Vesk</h1>
    <div class="icon-row">
      <span class="icon-row__rule icon-row__rule--left"></span>
      <svg class="icon" viewBox="0 0 20 20" aria-label="Phone" role="img">
        <rect x="0.5" y="0.5" width="19" height="19" rx="4" fill="var(--icon-fill)"/>
        <path d="M4 9 Q10 4 16 9 L14.5 10.5 L12.5 9 L12.5 8 Q10 7 7.5 8 L7.5 9 L5.5 10.5 Z" fill="var(--card-dark)"/>
        <rect x="6" y="11" width="8" height="4.5" rx="1" fill="var(--card-dark)"/>
      </svg>
      <svg class="icon" viewBox="0 0 20 20" aria-label="Mobile" role="img">
        <rect x="0.5" y="0.5" width="19" height="19" rx="4" fill="var(--icon-fill)"/>
        <rect x="6.5" y="3.5" width="7" height="13" rx="1.2" fill="var(--card-dark)"/>
        <rect x="7.6" y="5" width="4.8" height="8.5" fill="var(--icon-fill)"/>
      </svg>
      <svg class="icon" viewBox="0 0 20 20" aria-label="Email" role="img">
        <rect x="0.5" y="0.5" width="19" height="19" rx="4" fill="var(--icon-fill)"/>
        <rect x="4" y="6" width="12" height="8.5" fill="var(--card-dark)"/>
        <path d="M4.6 6.6 L10 11 L15.4 6.6 M4.6 14 L8.5 10 M15.4 14 L11.5 10" stroke="var(--icon-fill)" stroke-width="0.9" fill="none"/>
      </svg>
      <svg class="icon" viewBox="0 0 20 20" aria-label="Website" role="img">
        <rect x="0.5" y="0.5" width="19" height="19" rx="4" fill="var(--icon-fill)"/>
        <circle cx="10" cy="10" r="6" fill="var(--card-dark)"/>
        <path d="M4 10 H16 M10 4 V16" stroke="var(--icon-fill)" stroke-width="0.9"/>
      </svg>
      <span class="icon-row__rule icon-row__rule--right"></span>
    </div>
    <ul class="contact-list">
      <li class="contact-list__mobile">0438 260 947</li>
      <li class="contact-list__phone">02 7481 3926</li>
      <li class="contact-list__email">harold@1876basinsandspouts.com.au</li>
      <li class="contact-list__web">www.1876basinsandspouts.com.au</li>
    </ul>
  </section>

  <section class="card card--front" aria-label="Card front with business name">
    <div class="brand">
      <span class="brand__mark" aria-hidden="true"></span>
      <div class="brand__text">
        <p class="brand__name">1876 Basins &amp; Spouts</p>
        <p class="brand__tagline">Classic fittings crafted for everyday modern living</p>
      </div>
    </div>
  </section>
</main>
</body>
</html>
```